KTWG application splash screen

We need a 1024x768 image for use as an application splash screen.
The image will be displayed full screen on an 10 inch industrial PC 1024x768 screen while our application is launching. The image should convey that the application is "Waiting for connection to Wi-Fi access point..." and include a graphic of the industrial PC connected to the access point via an Ethernet cable. A list of troubleshooting steps should be included at the bottom of the image. The troubleshooting steps should not be the main focus of the image and should be shown in a smaller font (but still readable at 1024x768 displayed on a 10 inch screen).
I will include a mock up of the general idea of what we are looking for as well as image files for the industrial PC, a screenshot of our application to show on the PC's screen and the AP.
For general look and feel and a sense of corporate branding please review our website https://marrowgatesoilworks.example/. The splash screen should reflect corporate branding.
Target Market(s)
Users of our application
Industry/Entity Type
Agriculture
Look and feel

```html
<!DOCTYPE html>
<html lang="en">
<head>
<meta charset="utf-8">
<title>KTWG – Waiting for Wi-Fi access point</title>
<link rel="stylesheet" href="https://fonts.googleapis.com/css2?family=Poppins:wght@400;500;600;700&display=swap">
<style>
  :root {
    --green: #42bd6b;
    --white: #ffffff;
    --black: #000000;
    --device-dark: #2a2a2a;
    --device-mid: #4a4a4a;
    --ap-light: #f4f4f4;
    --ap-shade: #d9d9d9;
  }
  * { margin: 0; padding: 0; box-sizing: border-box; }
  html, body {
    width: 1200px; height: 1200px; overflow: hidden;
    background: var(--black);
    font-family: "Poppins", sans-serif;
  }
  .splash {
    position: absolute; left: 111px; top: 233px;
    width: 978px; height: 733px;
    background: var(--green);
    overflow: hidden;
  }
  .title-card {
    position: absolute; left: 229px; top: 0; width: 520px; height: 178px;
    background: var(--white);
    border-radius: 0 0 26px 26px;
    display: flex; align-items: center; justify-content: center;
  }
  .title-card h1 {
    color: var(--green); font-weight: 700; font-size: 42px;
    line-height: 44px; text-align: center; letter-spacing: 0.2px;
  }
  .device {
    position: absolute; left: 79px; top: 232px; width: 238px; height: 188px;
    border-radius: 14px;
    background: linear-gradient(160deg, var(--device-mid), var(--device-dark));
    border: 2px solid var(--white);
  }
  .access-point {
    position: absolute; left: 863px; top: 230px; width: 32px; height: 194px;
    border-radius: 6px;
    background: linear-gradient(90deg, var(--ap-shade), var(--ap-light) 40%, var(--ap-shade));
  }
  .cable { position: absolute; left: 0; top: 0; }
  .label {
    position: absolute; color: var(--white); text-transform: uppercase;
    letter-spacing: 1.5px; line-height: 1.1;
  }
  .label strong { display: block; font-weight: 700; font-size: 23px; }
  .label span { display: block; font-weight: 400; font-size: 16px; letter-spacing: 0.8px; }
  .label-computer { left: 332px; top: 308px; }
  .label-ap { right: 128px; top: 308px; text-align: right; }
  .label-cable {
    left: 0; width: 978px; top: 439px; text-align: center;
    font-weight: 700; font-size: 22px; letter-spacing: 1.5px;
  }
  .troubleshooting {
    position: absolute; left: 240px; top: 554px; width: 498px; height: 200px;
    background: var(--white); border-radius: 26px 26px 0 0;
    color: var(--green); padding-top: 12px;
  }
  .troubleshooting h2 {
    text-align: center; font-weight: 700; font-size: 16px; letter-spacing: 1.2px;
    margin-bottom: 2px;
  }
  .troubleshooting ul { list-style: none; font-size: 11.6px; line-height: 13.7px; }
  .troubleshooting li { position: relative; padding-left: 8px; }
  .troubleshooting > ul { margin-left: 27px; }
  .troubleshooting ul ul { margin-left: 15px; }
  .troubleshooting li::before { content: "•"; position: absolute; left: 0; }
  .brand {
    position: absolute; left: 852px; top: 648px;
    display: flex; align-items: center; gap: 6px;
    color: var(--black); font-weight: 700; font-size: 22px;
  }
  .brand-mark { width: 18px; height: 18px; background: var(--black); border-radius: 3px; }
</style>
</head>
<body>
<main class="splash">
  <header class="title-card">
    <h1>Waiting for<br>connection to Wi-Fi<br>access point...</h1>
  </header>

  <div class="device" role="img" aria-label="Industrial tablet PC showing the KTWG seeding application"></div>
  <div class="access-point" role="img" aria-label="Outdoor Wi-Fi access point with two antennas"></div>

  <svg class="cable" width="978" height="733" viewBox="0 0 978 733" aria-hidden="true">
    <polyline points="198,435 198,474 729,474 729,387 849,387"
      fill="none" stroke="#ffffff" stroke-width="4.5" stroke-linecap="round"
      stroke-dasharray="0 11.8"/>
  </svg>

  <div class="label label-computer"><strong>Tractor Cab</strong><span>Computer</span></div>
  <div class="label label-ap"><strong>Wi-Fi Access Point</strong><span>Norvane AX-200-Outdoor</span></div>
  <div class="label label-cable">Ethernet Cable</div>

  <section class="troubleshooting">
    <h2>TROUBLESHOOTING STEPS:</h2>
    <ul>
      <li>This screen should only be visible for a short time on boot.</li>
      <li>If this screen stays visible for more than a minute:
        <ul>
          <li>Verify that the Wi-Fi Access Point (AP) powers up when this system does (indicated by a green light on the side of the AP).</li>
          <li>Check the Ethernet cable between this system and the AP for damage, and replace it if necessary.</li>
          <li>Power-cycle this system and wait for it to reboot fully.</li>
          <li>If the issue persists, contact KTWG support for further assistance.</li>
        </ul>
      </li>
    </ul>
  </section>

  <div class="brand"><span class="brand-mark"></span>KTWG</div>
</main>
</body>
</html>
```